Birchwell Agency Condominium mail merge

We need a marketing proposal letter design to do a mail merge to potential e customers. We included our logo and an example of my miserable attempt to create a template. We are looking for a modern and attractive proposal template. Here is our website https://www.birchwellagency.example to be used for any additional information needed about us and our services.

Target Market(s)

New prospects

Industry/Entity Type

Insurance Agency

Requirements
Must have
• My project must have a modern professional look with merge fields similar to the file uploaded with this project.
Nice to have
• it would like have a condominium and a car icon graphic depicting there is additional discounts for both quotes bundled.
Should not have
• My project should not have any other logos or company name

```html
<!DOCTYPE html>
<html lang="en">
<head>
<meta charset="utf-8">
<title>Birchwell Agency – Condo Proposal Letter</title>
<link href="https://fonts.googleapis.com/css2?family=Poppins:wght@300;400;500;600;700&display=swap" rel="stylesheet">
<style>
  :root {
    --backdrop: #d4d4d4;
    --paper: #ffffff;
    --ink: #1f1f1f;
    --ink-soft: #5a5a5a;
    --ink-muted: #6e6e6e;
    --heading: #555555;
    --table-head: #3a3a3a;
    --row-alt: #ebebeb;
    --row-line: #cfcfcf;
    --premium: #b3ddf4;
    --accent-bar: #b3ddf4;
  }
  * { margin: 0; padding: 0; box-sizing: border-box; }
  html, body {
    width: 1037px; height: 1200px; overflow: hidden;
    background: var(--backdrop);
    font-family: "Poppins", sans-serif;
    color: var(--ink);
  }
  .letter {
    position: absolute; left: 98px; top: 11px;
    width: 840px; height: 1178px;
    background: var(--paper);
  }
  .brand {
    position: absolute; left: 44px; top: 70px;
    display: flex; align-items: center; gap: 10px;
    font-size: 26px; font-weight: 600; color: var(--ink);
  }
  .brand-dot { width: 26px; height: 26px; border-radius: 50%; background: var(--ink); }
  .agency-name {
    position: absolute; right: 37px; top: 52px;
    font-size: 28px; font-weight: 700; letter-spacing: 2px; color: var(--heading);
  }
  .letter-date {
    position: absolute; right: 42px; top: 92px;
    font-size: 12px; font-weight: 500;
  }
  .letter-date span { font-weight: 400; color: var(--ink-muted); letter-spacing: .5px; }
  .recipient {
    position: absolute; left: 49px; top: 188px;
    font-size: 12px; line-height: 22px;
  }
  .recipient .code { font-size: 16px; }
  .salutation { position: absolute; left: 49px; top: 370px; font-size: 12.5px; font-weight: 500; }
  .intro, .closing-text {
    position: absolute; left: 49px; width: 749px;
    font-size: 12.5px; line-height: 21px; color: var(--ink-soft); text-align: justify;
  }
  .intro { top: 396px; }
  .closing-text { top: 812px; line-height: 18px; text-align: left; }
  .closing-text b { color: var(--ink); font-weight: 600; }
  .coverage {
    position: absolute; left: 45px; top: 487px; width: 749px; height: 257px;
    border: 1px solid var(--row-line); border-top: none;
  }
  .coverage-head {
    height: 34px; background: var(--table-head); color: #fff;
    font-size: 13px; display: flex; align-items: center;
  }
  .coverage-head .c1 { padding-left: 26px; width: 288px; }
  .coverage-row {
    height: 27.6px; width: 472px; display: flex; align-items: center;
    font-size: 11px; color: var(--ink-muted);
  }
  .coverage-row:nth-child(odd) { background: var(--row-alt); }
  .coverage-row .c1 { padding-left: 22px; width: 289px; }
  .coverage-row.key { color: var(--ink); font-weight: 500; }
  .premium-panel {
    position: absolute; left: 472px; top: 35px; width: 276px; height: 221px;
    background: var(--premium);
    display: flex; flex-direction: column; align-items: center; justify-content: center;
    gap: 8px; font-size: 14.5px; font-weight: 600;
  }
  .footnote {
    position: absolute; left: 57px; top: 750px; width: 730px;
    font-size: 11px; line-height: 15px; font-weight: 500;
  }
  .signoff { position: absolute; left: 44px; top: 895px; font-size: 12.5px; letter-spacing: .5px; }
  .signature {
    position: absolute; left: 44px; top: 926px; width: 140px; height: 36px;
    background: linear-gradient(90deg, #e8e6f1, #f4f3f8);
  }
  .signature-rule { position: absolute; left: 44px; top: 971px; width: 144px; height: 1px; background: #999; }
  .signer-role {
    position: absolute; left: 44px; top: 980px;
    font-size: 11.5px; font-weight: 500; letter-spacing: 1.5px;
  }
  .contact {
    position: absolute; left: 44px; top: 1084px;
    font-size: 12.5px; line-height: 21px; letter-spacing: .3px;
  }
  .contact b { font-weight: 600; }
  .footer-bar {
    position: absolute; left: 42px; top: 1135px; width: 758px; height: 8px;
    border-radius: 4px; background: var(--accent-bar);
  }
  .bundle-badge {
    position: absolute; left: 621px; top: 1037px; width: 191px; height: 102px;
    border-radius: 8px;
    background: linear-gradient(180deg, #c7e6f8 0%, #a9d4ee 100%);
  }
</style>
</head>
<body>
  <main class="letter">
    <div class="brand"><span class="brand-dot"></span>Harborline</div>

    <h1 class="agency-name">BIRCHWELL AGENCY</h1>
    <p class="letter-date">Date: <span>&lt;&lt;DATE&gt;&gt;</span></p>

    <address class="recipient" style="font-style:normal">
      <div class="code">«encodedimbno»</div>
      <div>«first_name» «last_name»</div>
      <div>&lt;&lt;Address&gt;&gt;</div>
      <div>&lt;&lt;Address2&gt;&gt;</div>
      <div>&lt;&lt;City&gt;&gt;, &lt;&lt;State&gt;&gt;, &lt;&lt;Zip&gt;&gt;</div>
      <div class="code">«presorttrayid»</div>
    </address>

    <p class="salutation">Respected Sir,</p>
    <p class="intro">We have saved our clients $100s on their Condo Insurance. Call us at 407-555-0142 so we can do the same for you! Bundle your Condo and Auto insurance together for additional savings with a multi-policy discount. Below is a sample Condo Insurance policy purchased recently in Orlando from Birchwell Insurance Agency.</p>

    <section class="coverage">
      <div class="coverage-head"><span class="c1">COVERAGE</span><span>LIMIT</span></div>
      <div class="coverage-rows">
        <div class="coverage-row" style="background:#fff"><span class="c1">Personal Property Protection</span><span>&lt;ColumnQ&gt;</span></div>
        <div class="coverage-row" style="background:var(--row-alt)"><span class="c1">Increased Additional Living Expense</span><span>20%</span></div>
        <div class="coverage-row" style="background:#fff"><span class="c1">Loss Assessments</span><span>$2,000</span></div>
        <div class="coverage-row" style="background:var(--row-alt)"><span class="c1">Family Liability Protection</span><span>$100,000</span></div>
        <div class="coverage-row" style="background:#fff"><span class="c1">Building Property Protection</span><span>&lt;ColumnK&gt;</span></div>
        <div class="coverage-row" style="background:var(--row-alt)"><span class="c1">Building Codes Coverages</span><span>25%</span></div>
        <div class="coverage-row key" style="background:#fff"><span class="c1">All Perils Deductible</span><span>$500</span></div>
        <div class="coverage-row key" style="background:var(--row-alt)"><span class="c1">Hurricane&nbsp; Deductible</span><span>$500</span></div>
      </div>
      <div class="premium-panel">
        <span>Total Annual Premium:</span>
        <span>&lt;&lt;Yearly Premium&gt;&gt;</span>
      </div>
    </section>

    <p class="footnote">***The quoted premium is a sample premium based on a recent policy purchased in Orlando. Premium will differ based on information obtained on your application***</p>

    <p class="closing-text">If you are tired of paying too much for Condo Insurance and are wanting all of your insurance needs handled under one agency, then call us at <b>407-555.0142</b>. One call is all it takes to see if you've got the right coverage at the right price.</p>

    <p class="signoff">Sincerely,</p>
    <div class="signature" role="img" aria-label="Handwritten signature of Marcus Birchwell"></div>
    <div class="signature-rule"></div>
    <p class="signer-role">[ AGENCY PRINCIPAL ]</p>

    <div class="contact">
      <div><b>A:</b> 2740 Maple Crest Road Ste. 210 Lakeview, FL 32700</div>
      <div><b>P:</b> 02 5550 1234 00 <b>E:</b> info@BirchwellAgency.example, <b>W:</b> BirchwellAgency.example</div>
    </div>
    <div class="footer-bar"></div>
    <div class="bundle-badge" role="img" aria-label="Illustration of a house plus a car with a Combine and Save bundle discount message"></div>
  </main>
</body>
</html>
```